Professional, modern and unique business card. We are looking to present a new look to our business cards however we don't want to divert too far away from original template. We want social media links and our 3 office addresses on the backside of the business cards. Please see attached business card templates for ideas.
Crestline Homes Color Code:
R: 7
G:63
B:86

Target Market(s)

Real Estate

Industry/Entity Type

Real Estate

Contact Information for Business Card

Follow the attached templates. In need of a more modern and unique touch but don't want to divert from the original theme or color.
Crestline Homes Color Code:
R: 7
G:63
B:86

Font styles to use
Serif

Requirements
Must have
• Crestline Homes logo, Crestline homes colors, social media links, 3 office addresses,
Nice to have
• information about Crestline Homes and QR codes. You can check out www.mycrestlinehomes.example

```html
<!DOCTYPE html>
<html lang="en">
<head>
<meta charset="UTF-8">
<title>Crestline Homes Business Card</title>
<link href="https://fonts.googleapis.com/css2?family=Lato:wght@400;700&display=swap" rel="stylesheet">
<style>
  :root {
    --page-bg: #e6e6e6;
    --card-navy: #073f56;
    --text-light: #e3eef3;
    --text-soft: #b9ccd5;
    --rule: rgba(227, 238, 243, 0.35);
    --logo-tint: #dcebf2;
    --dot-blue: #3b5998;
    --dot-red: #c9302c;
    --dot-link: #1f6fa8;
    --dot-sky: #2ea5dd;
  }
  * { box-sizing: border-box; margin: 0; padding: 0; }
  html, body { width: 1200px; height: 900px; overflow: hidden; }
  body {
    background: var(--page-bg);
    font-family: "Lato", Arial, sans-serif;
    color: var(--text-light);
    position: relative;
  }
  .card {
    position: absolute;
    width: 700px;
    height: 400px;
    background: var(--card-navy);
    border-radius: 30px;
    box-shadow: 0 6px 18px rgba(0,0,0,0.18);
  }
  .card-back { left: 110px; top: 40px; }
  .card-front { left: 390px; top: 460px; }

  .brand-name {
    position: absolute;
    font-family: "Lato", Arial, sans-serif;
    font-weight: 700;
    color: var(--logo-tint);
    letter-spacing: 1px;
    line-height: 1;
    white-space: nowrap;
  }
  .brand-name .brand-dot {
    display: inline-block;
    width: 16px; height: 16px;
    border-radius: 50%;
    background: var(--logo-tint);
    margin-left: 10px;
    vertical-align: middle;
  }

  /* back side */
  .card-back .brand-name { left: 46px; top: 178px; font-size: 36px; }
  .back-divider {
    position: absolute;
    left: 350px; top: 40px;
    width: 1px; height: 240px;
    background: var(--rule);
  }
  .social-list {
    position: absolute;
    left: 372px; top: 42px;
    list-style: none;
  }
  .social-list li {
    display: flex; align-items: center;
    font-size: 17px;
    height: 36px;
  }
  .social-dot {
    width: 20px; height: 20px; border-radius: 50%;
    margin-right: 10px; flex: none;
  }
  .dot-blue { background: var(--dot-blue); }
  .dot-red { background: var(--dot-red); }
  .dot-link { background: var(--dot-link); }
  .dot-sky { background: var(--dot-sky); }

  .office-list {
    position: absolute;
    left: 40px; right: 30px; bottom: 34px;
    display: flex;
  }
  .office {
    font-size: 15.5px;
    line-height: 1.25;
    color: var(--text-soft);
    padding: 0 16px;
    border-left: 1px solid var(--rule);
    white-space: nowrap;
  }
  .office:first-child { border-left: none; padding-left: 0; }

  /* front side */
  .card-front .brand-name { left: 370px; top: 96px; font-size: 36px; }
  .front-rule {
    position: absolute;
    left: 210px; top: 196px;
    width: 450px; height: 1px;
    background: var(--rule);
  }
  .person {
    position: absolute;
    left: 42px; top: 214px;
  }
  .person-name { font-size: 23px; font-weight: 700; letter-spacing: 0.5px; }
  .person-role { font-size: 17px; margin-top: 2px; }
  .phone-list { list-style: none; margin-top: 22px; }
  .phone-list li {
    display: flex; align-items: center;
    font-size: 18px; height: 25px;
  }
  .phone-list svg { width: 16px; height: 16px; margin-right: 10px; fill: var(--text-light); }

  .web-contacts {
    position: absolute;
    right: 36px; top: 220px;
    list-style: none;
    text-align: right;
  }
  .web-contacts li {
    display: flex; justify-content: flex-end; align-items: center;
    font-size: 16px; height: 26px;
  }
  .web-contacts svg { width: 14px; height: 14px; margin-left: 8px; fill: var(--text-light); }
</style>
</head>
<body>

<section class="card card-back" aria-label="Business card back">
  <div class="brand-name">Crestline Homes<span class="brand-dot"></span></div>
  <div class="back-divider"></div>
  <ul class="social-list">
    <li><span class="social-dot dot-blue"></span>CrestlinehomesNY</li>
    <li><span class="social-dot dot-red"></span>Info at Crestline Homes New York</li>
    <li><span class="social-dot dot-link"></span>Crestline Homes</li>
    <li><span class="social-dot dot-red"></span>Crestline Homes</li>
    <li><span class="social-dot dot-sky"></span>@CrestlineHomesQ</li>
  </ul>
  <div class="office-list">
    <address class="office">418-20 Harbor Crest Rd<br>Bay Hollow, NY 11590</address>
    <address class="office">72-40 Maple Ridge Blvd<br>Elm Terrace, NY 11593</address>
    <address class="office">905 Summit Ave<br>Stonebridge, NY 11596</address>
  </div>
</section>

<section class="card card-front" aria-label="Business card front">
  <div class="brand-name">Crestline Homes<span class="brand-dot"></span></div>
  <div class="front-rule"></div>
  <div class="person">
    <div class="person-name">DANIEL WHITFORD</div>
    <div class="person-role">Managing Director</div>
    <ul class="phone-list">
      <li><svg viewBox="0 0 16 16" aria-hidden="true"><path d="M1 5c0-2 2-3 7-3s7 1 7 3v1h-4V5H5v1H1zM3 8h10l1 6H2z"/></svg>055-210 384 617</li>
      <li><svg viewBox="0 0 16 16" aria-hidden="true"><path d="M4 1h8v14H4zM5.5 3v9h5V3z"/></svg>055-210 384 618</li>
      <li><svg viewBox="0 0 16 16" aria-hidden="true"><path d="M4 1h8v4H4zM1 6h14v7h-3v2H4v-2H1zM5 10v4h6v-4z"/></svg>055-210 384 619</li>
    </ul>
  </div>
  <ul class="web-contacts">
    <li>info@crestline.example<svg viewBox="0 0 16 16" aria-hidden="true"><path d="M1 3h14v10H1zM2.5 4.5 8 9l5.5-4.5z"/></svg></li>
    <li>www.mycrestlinehomes.example<svg viewBox="0 0 16 16" aria-hidden="true"><circle cx="8" cy="8" r="7"/></svg></li>
  </ul>
</section>

</body>
</html>
```